RWT Fittings Ltd Business Cards

We need a business card with our business logo. We provide window and door installations on high-rises in west coast British Colombia, Canada.

I would like my business information and details on one side of the card, and the other side the company name with logo

Target Market(s)

General Contractors

Industry/Entity Type

Construction

Contact Information for Business Card

one side i want my company name and logo in the dark theme logo that i provided

Requirements
Must have
• Marco Peltieri, 16045518293, RWTFittings@mailbox-demo.com, 1407-5194 Linden Row Burnaby BC, V5H 2K9, Owner & Manager

```html
<!DOCTYPE html>
<html lang="en">
<head>
<meta charset="UTF-8">
<title>RWT Fittings Ltd — Business Cards</title>
<link rel="stylesheet" href="https://fonts.googleapis.com/css2?family=Roboto:wght@400;500;700&display=swap">
<style>
  :root {
    --backdrop: #222224;
    --card: #1f2026;
    --brand-blue: #29abe2;
    --name-grey: #a9a9ad;
    --text-white: #f2f2f2;
    --divider: #8a8a90;
    --emboss: #2e3038;
  }
  * { box-sizing: border-box; margin: 0; padding: 0; }
  html, body {
    width: 1200px; height: 780px; overflow: hidden;
    background: var(--backdrop);
    font-family: "Roboto", Arial, sans-serif;
  }
  .sheet {
    position: relative; width: 1200px; height: 780px;
    display: flex; align-items: center; justify-content: center; gap: 40px;
  }
  .card {
    position: relative; width: 540px; height: 309px;
    background: var(--card);
    box-shadow: 0 18px 40px rgba(0,0,0,0.45);
    overflow: hidden;
  }
  /* Front: contact side */
  .brand-mark {
    position: absolute; top: 48px; left: 205px;
    display: flex; align-items: center; gap: 12px;
  }
  .brand-mark .badge {
    width: 34px; height: 34px; background: var(--brand-blue);
  }
  .brand-name {
    font-weight: 700; font-size: 27px; color: var(--brand-blue);
    letter-spacing: 0.5px; white-space: nowrap;
  }
  .holder {
    position: absolute; top: 142px; left: 42px;
  }
  .holder-name {
    font-weight: 700; font-size: 25px; line-height: 1;
  }
  .holder-name .first { color: var(--brand-blue); }
  .holder-name .last { color: var(--name-grey); }
  .holder-role {
    margin-top: 6px; font-size: 13px; color: var(--text-white);
    text-align: right;
  }
  .divider {
    position: absolute; top: 140px; left: 258px;
    width: 1px; height: 78px; background: var(--divider);
    transform: rotate(-30deg);
  }
  .contact {
    position: absolute; top: 158px; left: 300px;
    list-style: none; display: flex; flex-direction: column; gap: 9px;
  }
  .contact li {
    display: flex; align-items: center; gap: 9px;
    font-size: 14px; color: var(--text-white);
  }
  .contact svg { width: 14px; height: 14px; flex: none; }
  .address-band {
    position: absolute; left: 0; right: 0; bottom: 0; height: 38px;
    background: var(--brand-blue);
    display: flex; align-items: center; padding-left: 42px;
    font-size: 14px; color: var(--text-white); font-weight: 500;
  }
  /* Back: brand side */
  .card-back {
    display: flex; align-items: center; justify-content: center; gap: 14px;
  }
  .card-back .badge {
    width: 44px; height: 44px; background: var(--emboss);
  }
  .card-back .brand-name {
    font-size: 38px; color: var(--emboss);
  }
</style>
</head>
<body>
<main class="sheet">
  <section class="card card-front" aria-label="Card front with contact details">
    <div class="brand-mark">
      <span class="badge"></span>
      <span class="brand-name">RWT Fittings Ltd</span>
    </div>

    <div class="holder">
      <h1 class="holder-name"><span class="first">Marco</span> <span class="last">Peltieri</span></h1>
      <p class="holder-role">Owner &amp; Manager</p>
    </div>

    <span class="divider"></span>

    <ul class="contact">
      <li>
        <svg viewBox="0 0 24 24" aria-hidden="true"><path fill="#29abe2" d="M6.6 10.8a15.1 15.1 0 0 0 6.6 6.6l2.2-2.2a1 1 0 0 1 1-.25 11.4 11.4 0 0 0 3.6.57 1 1 0 0 1 1 1V20a1 1 0 0 1-1 1A17 17 0 0 1 3 4a1 1 0 0 1 1-1h3.5a1 1 0 0 1 1 1c0 1.25.2 2.45.57 3.57a1 1 0 0 1-.25 1z"/></svg>
        <span>1604 551 8293</span>
      </li>
      <li>
        <svg viewBox="0 0 24 24" aria-hidden="true"><rect x="2" y="5" width="20" height="14" rx="1.5" fill="#29abe2"/><path d="M3 6l9 7 9-7" fill="none" stroke="#1f2026" stroke-width="1.8"/></svg>
        <span>RWTFittings@mailbox-demo.com</span>
      </li>
    </ul>

    <div class="address-band">1407-5194 Linden Row Burnaby BC, V5H 2K9</div>
  </section>

  <section class="card card-back" aria-label="Card back with company name">
    <span class="badge"></span>
    <span class="brand-name">RWT Fittings Ltd</span>
  </section>
</main>
</body>
</html>
```